English and Spanish Language School Needs a Business Card

Need a business card design a startup company called Maribel Language School. The company will offer English and Spanish conversational level courses designed to make the learner feel comfortable with grammar and vocabulary. We would like to see a logo with some colour that should communicate learning, growth.

Target Market(s)

Consumers and businesses

Industry/Entity Type

Education

Contact Information for Business Card

TBD

Font styles to use
Serif

Requirements
Must have
• Include the following
• Logo
• Name
• Title
• Cellphone Number
• Office Phone number
• Email address
• Office Address

```html
<!DOCTYPE html>
<html lang="en">
<head>
<meta charset="utf-8">
<title>Maribel Language School – Business Card</title>
<link rel="stylesheet" href="https://fonts.googleapis.com/css2?family=Open+Sans:wght@400;600;700&display=swap">
<style>
  :root {
    --stage: #000000;
    --card-front: #a82225;
    --card-back: #272626;
    --ink: #ffffff;
    --rule: #d9777a;
  }
  html, body {
    margin: 0;
    padding: 0;
    width: 1200px;
    height: 900px;
    overflow: hidden;
    background: var(--stage);
  }
  .stage {
    position: relative;
    width: 1200px;
    height: 900px;
    font-family: "Open Sans", sans-serif;
    color: var(--ink);
  }
  .card {
    position: absolute;
    top: 275px;
    width: 477px;
    height: 294px;
    box-sizing: border-box;
  }
  .card--front {
    left: 116px;
    background: var(--card-front);
    border-radius: 0 52px 0 52px;
  }
  .card--back {
    left: 622px;
    background: var(--card-back);
    border-radius: 52px 0 52px 0;
  }
  .brand {
    position: absolute;
    font-weight: 600;
    color: var(--ink);
    line-height: 1;
    margin: 0;
  }
  .brand__name {
    display: block;
    font-size: 58px;
    letter-spacing: -1px;
  }
  .brand__tagline {
    display: block;
    font-size: 15px;
    margin-top: 2px;
  }
  .card--front .brand {
    right: 36px;
    top: 44px;
    text-align: right;
  }
  .card--back .brand {
    left: 0;
    right: 0;
    top: 103px;
    text-align: center;
  }
  .holder {
    position: absolute;
    left: 37px;
    top: 130px;
    width: 404px;
  }
  .holder__name {
    margin: 0;
    font-size: 17px;
    font-weight: 700;
    line-height: 22px;
  }
  .holder__rule {
    height: 1px;
    background: var(--rule);
    margin: 6px 0 6px;
  }
  .holder__title {
    margin: 0;
    font-size: 14px;
    line-height: 18px;
  }
  .contacts {
    position: absolute;
    left: 37px;
    top: 198px;
    margin: 0;
    padding: 0;
    list-style: none;
    font-size: 12.5px;
    line-height: 18px;
  }
  .contacts__item {
    display: flex;
    align-items: center;
    gap: 6px;
  }
  .contacts__icon {
    width: 9px;
    height: 9px;
    fill: var(--ink);
  }
  .address {
    position: absolute;
    right: 36px;
    top: 214px;
    margin: 0;
    font-style: normal;
    font-size: 12.5px;
    line-height: 19px;
    text-align: right;
  }
</style>
</head>
<body>
<main class="stage">
  <section class="card card--front" aria-label="Business card front">
    <h1 class="brand">
      <span class="brand__name">Maribel</span>
      <span class="brand__tagline">Language School</span>
    </h1>
    <div class="holder">
      <p class="holder__name">Daniel Fortier</p>
      <div class="holder__rule"></div>
      <p class="holder__title">President</p>
    </div>
    <ul class="contacts">
      <li class="contacts__item">
        <svg class="contacts__icon" viewBox="0 0 10 10" aria-hidden="true"><path d="M2 0.5 L3.6 2.6 L2.8 3.6 Q4 6 6.4 7.2 L7.4 6.4 L9.5 8 L8.3 9.5 Q2.6 9 0.5 1.7 Z"/></svg>
        <span>645-4821-017</span>
      </li>
      <li class="contacts__item">
        <svg class="contacts__icon" viewBox="0 0 10 10" aria-hidden="true"><path d="M0.5 3.5 Q5 0.5 9.5 3.5 L8.6 5 L7 4.2 L7 3.3 Q5 2.6 3 3.3 L3 4.2 L1.4 5 Z"/><rect x="2.2" y="5.5" width="5.6" height="3.5" rx="0.6"/></svg>
        <span>(514)555-0142</span>
      </li>
      <li class="contacts__item">
        <svg class="contacts__icon" viewBox="0 0 10 10" aria-hidden="true"><rect x="0.5" y="2" width="9" height="6.5"/><path d="M0.5 2 L5 5.6 L9.5 2" fill="none" stroke="#a82225" stroke-width="1"/></svg>
        <span>hello@maribelschool.com</span>
      </li>
    </ul>
    <address class="address">
      4370 Rue des Érables<br>
      Montreal, QC, H2K3B9
    </address>
  </section>

  <section class="card card--back" aria-label="Business card back">
    <h2 class="brand">
      <span class="brand__name">Maribel</span>
      <span class="brand__tagline">Language School</span>
    </h2>
  </section>
</main>
</body>
</html>
```